Cash Pay Massage Therapy Services for Medical & Therapy Clinics

We are rolling out a new Massage Therapy service in our medical clinics, staffed by licensed professionals. Our offices have a feel between medical clinic and spa. We would like to have some small 8.5x11 posters that let the patients know that we also provide Massages at $80/60 minutes and $50/30 minutes. Typically we always bill insurance but this service would accept cash or credit card.

Target Market(s)

patients that are already having services in our medical offices. Typically, they are already being seen for massage therapy that is billing to their insurance. But, they love their therapist and want to continue to see them when insurance doesnt pay anymore.

Industry/Entity Type

Massage Therapy

Requirements
Must have
• professional (more rehabilitative/less spa) appearance. Prices, logo
Nice to have
• a similar aesthetic to our website.

```html
<!DOCTYPE html>
<html lang="en">
<head>
<meta charset="utf-8">
<title>Restora – Massage Therapy Poster</title>
<link href="https://fonts.googleapis.com/css2?family=Lato:wght@400;700;900&family=Oswald:wght@600;700&display=swap" rel="stylesheet">
<style>
  :root {
    --page-bg: #e9e9e9;
    --ink: #1c1c1c;
    --white: #ffffff;
    --panel: #f3f3f3;
    --brand-blue: #1ba3e3;
    --brand-green: #8dc21f;
    --logo-black: #000000;
    --photo-light: #e4e1dc;
    --photo-mid: #b9aea3;
    --photo-dark: #5a4a3e;
  }
  html, body {
    margin: 0;
    width: 1020px;
    height: 1200px;
    overflow: hidden;
    background: var(--page-bg);
  }
  .poster {
    position: absolute;
    left: 63px;
    top: 20px;
    width: 894px;
    height: 1160px;
    display: block;
    box-shadow: 0 4px 16px rgba(0,0,0,.18);
  }
  .body-text { font-family: "Lato", sans-serif; fill: var(--ink); }
  .headline { font-family: "Lato", sans-serif; font-weight: 900; fill: var(--ink); }
  .price { font-family: "Oswald", sans-serif; font-weight: 700; fill: var(--white); }
  .price-unit { font-family: "Lato", sans-serif; font-weight: 400; fill: var(--white); }
  .contact { font-family: "Lato", sans-serif; font-weight: 700; fill: var(--white); }
  .brand-name { font-family: "Lato", sans-serif; font-weight: 400; fill: var(--white); }
</style>
</head>
<body>
<svg class="poster" viewBox="0 0 663 860" xmlns="http://www.w3.org/2000/svg">
  <defs>
    <linearGradient id="clinicPhotoTone" x1="0" y1="0" x2="1" y2="1">
      <stop offset="0" stop-color="var(--photo-light)"/>
      <stop offset="0.55" stop-color="var(--photo-mid)"/>
      <stop offset="1" stop-color="var(--photo-dark)"/>
    </linearGradient>
    <linearGradient id="stretchPhotoTone" x1="0" y1="0" x2="1" y2="1">
      <stop offset="0" stop-color="#cfe6f3"/>
      <stop offset="1" stop-color="#6fa6cc"/>
    </linearGradient>
    <linearGradient id="shoulderPhotoTone" x1="0" y1="0" x2="1" y2="1">
      <stop offset="0" stop-color="#f1efec"/>
      <stop offset="1" stop-color="#b8aaa0"/>
    </linearGradient>
    <clipPath id="posterClip"><rect width="663" height="860"/></clipPath>
  </defs>

  <g clip-path="url(#posterClip)">
    <rect class="poster-base" width="663" height="860" fill="var(--white)"/>

    <!-- hero photograph area -->
    <rect class="hero-photo" x="0" y="0" width="663" height="500" fill="url(#clinicPhotoTone)"
          role="img" aria-label="Photo: doctor talking with a smiling senior patient in a clinic room"/>

    <!-- logo block -->
    <g class="brand-logo">
      <rect x="456" y="32" width="174" height="85" fill="var(--logo-black)"/>
      <text class="brand-name" x="543" y="88" font-size="34" text-anchor="middle">restora</text>
    </g>

    <!-- curved content panel -->
    <path class="panel-blue-arc" d="M0 455 C120 380 300 345 470 360 C560 370 630 400 663 430 L663 860 L0 860 Z" fill="var(--brand-blue)"/>
    <path class="panel" d="M0 520 C110 420 280 378 460 388 C560 396 630 430 663 470 L663 860 L0 860 Z" fill="var(--panel)"/>
    <path class="panel-right-band" d="M610 470 C640 510 660 560 663 600 L663 470 Z" fill="var(--brand-blue)"/>

    <!-- round photos -->
    <g class="photo-circle small">
      <circle cx="349" cy="412" r="80" fill="var(--brand-green)"/>
      <circle cx="345" cy="408" r="76" fill="var(--white)"/>
      <circle cx="345" cy="408" r="68" fill="url(#stretchPhotoTone)"
              role="img" aria-label="Photo: therapist stretching a patient's leg"/>
    </g>
    <g class="photo-circle large">
      <circle cx="510" cy="490" r="122" fill="var(--brand-green)"/>
      <circle cx="505" cy="483" r="117" fill="var(--white)"/>
      <circle cx="505" cy="483" r="107" fill="url(#shoulderPhotoTone)"
              role="img" aria-label="Photo: therapist treating a man's shoulder"/>
    </g>

    <!-- headline -->
    <text class="body-text" x="72" y="505" font-size="21">We Also Provide</text>
    <text class="headline" x="72" y="548" font-size="34">MASSAGES AT</text>

    <!-- price tags -->
    <g class="price-tag">
      <rect x="70" y="580" width="245" height="46" rx="3" fill="var(--brand-blue)"/>
      <rect x="83" y="571" width="97" height="64" fill="var(--brand-green)"/>
      <text class="price" x="131" y="621" font-size="38" text-anchor="middle">$80</text>
      <text class="price-unit" x="186" y="610" font-size="19">/60 minutes</text>
    </g>
    <text class="body-text" x="243" y="657" font-size="20" text-anchor="middle">and</text>
    <g class="price-tag">
      <rect x="70" y="671" width="245" height="46" rx="3" fill="var(--brand-blue)"/>
      <rect x="83" y="662" width="97" height="64" fill="var(--brand-green)"/>
      <text class="price" x="131" y="712" font-size="38" text-anchor="middle">$50</text>
      <text class="price-unit" x="186" y="701" font-size="19">/30 minutes</text>
    </g>

    <!-- payment note -->
    <g class="payment-note body-text" font-size="18" text-anchor="middle">
      <text x="512" y="664">Typically we always</text>
      <text x="512" y="688">bill insurance but</text>
      <text x="512" y="712">this service would accept</text>
      <text x="512" y="736">cash or credit card.</text>
    </g>

    <!-- footer bands -->
    <path class="footer-white" d="M0 760 C160 720 380 718 663 790 L663 860 L0 860 Z" fill="var(--white)"/>
    <path class="footer-blue" d="M0 772 C170 732 390 732 663 808 L663 860 L0 860 Z" fill="var(--brand-blue)"/>
    <path class="footer-green" d="M0 790 C180 752 400 760 600 860 L0 860 Z" fill="var(--brand-green)"/>

    <!-- contact -->
    <g class="contact-phone">
      <circle cx="92" cy="800" r="8" fill="none" stroke="var(--white)" stroke-width="1.6"/>
      <path d="M88.5 795.5 l2 -0.5 l1.3 2.8 l-1.2 1 c0.6 1.4 1.6 2.4 3 3 l1 -1.2 l2.8 1.3 l-0.5 2 c-4.5 0.3 -8.7 -3.9 -8.4 -8.4 z" fill="var(--white)"/>
      <text class="contact" x="114" y="808" font-size="22">555 014 2290</text>
    </g>
    <g class="contact-web">
      <circle cx="92" cy="833" r="8" fill="none" stroke="var(--white)" stroke-width="1.6"/>
      <ellipse cx="92" cy="833" rx="3.5" ry="8" fill="none" stroke="var(--white)" stroke-width="1.2"/>
      <line x1="84" y1="833" x2="100" y2="833" stroke="var(--white)" stroke-width="1.2"/>
      <text class="contact" x="114" y="840" font-size="20">www.restoraclinics.com</text>
    </g>
  </g>
</svg>
</body>
</html>
```